I need a business card designed using the logo provided either vertical or horizontal......Harbourline Property Group is an Australian based real estate company that caters for the upper end of the market so the design of the business card "must reflect" the companies image!!
Colour combinations are optional but "must be realistic" and must be able to be accurately useable CMYK colours.
Please consider that any colours used "must be able to be used" and be suitable in following designs for "pull out banner signs" and "real estate signs".
The colours and the font in the attached designs are for example and other combinations are encouraged.
Target Market(s)
The High End of the Australian real estate market
Industry/Entity Type
Business
Contact Information for Business Card
Logo - Business Name - Director + Licensed Real Estate Agent - Mobile Number (Cell Phone) - Business Number - Fax - Email Address - Web address
Requirements
Must have
- Designs and colours (CMYK) that can easily be interpreted by an Australian printer.
Nice to have
- Some alternative ideas on colour and font..........the ones provided are ok and have been provided as an example but I am looking for alternative ideas
Should not have
- Loud, overly bright colours. Designs that do not reflect the professional standards of the business.
- Designs that look good on a computer monitor but can not be re-created on a printing press.............this is most important when it comes to shading etc.

```html
<!DOCTYPE html>
<html lang="en">
<head>
<meta charset="utf-8">
<title>Harbourline Property Group — Business Card</title>
<link rel="stylesheet" href="https://fonts.googleapis.com/css2?family=Ubuntu:wght@400;500;700&display=swap">
<style>
  :root {
    --page: #ecebe8;
    --card: #ffffff;
    --gold: #c6a034;
    --gold-deep: #a5832a;
    --ink: #1f1f1f;
    --ink-soft: #333333;
    --on-gold: #ffffff;
  }
  html, body {
    margin: 0;
    width: 1200px;
    height: 818px;
    overflow: hidden;
    background: var(--page);
    font-family: "Ubuntu", sans-serif;
  }
  .card {
    position: absolute;
    left: 100px;
    top: 123px;
    width: 1000px;
    height: 571px;
    background: var(--card);
    box-shadow: 0 6px 24px rgba(0,0,0,0.12);
    overflow: hidden;
  }
  .card__band {
    position: absolute;
    inset: 0;
  }
  .holder {
    position: absolute;
    right: 190px;
    top: 14px;
    text-align: right;
    color: var(--on-gold);
  }
  .holder__name {
    font-size: 40px;
    font-weight: 700;
    line-height: 1.1;
  }
  .holder__title {
    font-size: 19px;
    font-weight: 400;
    margin-top: 2px;
  }
  .brand {
    position: absolute;
    left: 690px;
    top: 255px;
    display: flex;
    align-items: center;
    gap: 16px;
  }
  .brand__dot {
    width: 36px;
    height: 36px;
    border-radius: 50%;
    background: var(--gold);
    flex: none;
  }
  .brand__name {
    font-size: 30px;
    font-weight: 500;
    line-height: 1.1;
    color: var(--ink-soft);
  }
  .company {
    position: absolute;
    left: 90px;
    top: 200px;
    color: var(--ink);
  }
  .company__name {
    font-size: 36px;
    font-weight: 400;
    margin: 0 0 6px;
  }
  .company__address {
    font-size: 21px;
    line-height: 1.3;
    margin: 0;
    padding-left: 40px;
  }
  .contacts {
    position: absolute;
    left: 170px;
    top: 350px;
    list-style: none;
    margin: 0;
    padding: 0;
    color: var(--ink);
    font-size: 20px;
  }
  .contacts__item {
    display: flex;
    align-items: center;
    gap: 14px;
    height: 34px;
  }
  .contacts__icon {
    width: 24px;
    height: 24px;
    flex: none;
  }
</style>
</head>
<body>
  <div class="card">
    <svg class="card__band" viewBox="0 0 1000 571" width="1000" height="571" aria-hidden="true">
      <defs>
        <linearGradient id="goldFill" x1="0" y1="0" x2="1" y2="1">
          <stop offset="0" stop-color="#cfab3e"/>
          <stop offset="1" stop-color="#a5832a"/>
        </linearGradient>
      </defs>
      <path d="M0 0 H1000 V190 C880 178 760 132 560 112 C360 92 220 40 0 86 Z" fill="url(#goldFill)"/>
    </svg>

    <div class="holder">
      <div class="holder__name">Employee Name</div>
      <div class="holder__title">Director · Licensed Real Estate Agent</div>
    </div>

    <div class="brand">
      <span class="brand__dot"></span>
      <span class="brand__name">Harbourline<br>Property Group</span>
    </div>

    <div class="company">
      <h1 class="company__name">Harbourline Property Group</h1>
      <p class="company__address">18 Wharf Street Sydney<br>NSW 2000</p>
    </div>

    <ul class="contacts">
      <li class="contacts__item">
        <svg class="contacts__icon" viewBox="0 0 24 24"><rect width="24" height="24" rx="4" fill="var(--gold)"/><rect x="8" y="4.5" width="8" height="15" rx="1.5" fill="none" stroke="#fff" stroke-width="1.5"/><circle cx="12" cy="16.8" r="0.9" fill="#fff"/></svg>
        <span>M 0400 218 736</span>
      </li>
      <li class="contacts__item">
        <svg class="contacts__icon" viewBox="0 0 24 24"><rect width="24" height="24" rx="4" fill="var(--gold)"/><path d="M7 6 L10 6 L11 9 L9.5 10.5 C10.5 12.5 11.5 13.5 13.5 14.5 L15 13 L18 14 L18 17 C12 17.5 6.5 12 7 6 Z" fill="#fff"/></svg>
        <span>P 02 9214 5580</span>
      </li>
      <li class="contacts__item">
        <svg class="contacts__icon" viewBox="0 0 24 24"><rect width="24" height="24" rx="4" fill="var(--gold)"/><rect x="8" y="5" width="8" height="5" fill="none" stroke="#fff" stroke-width="1.4"/><rect x="5" y="10" width="14" height="6" rx="1" fill="#fff"/><rect x="8" y="14" width="8" height="5" fill="var(--gold)" stroke="#fff" stroke-width="1.4"/></svg>
        <span>F 02 9214 5581</span>
      </li>
      <li class="contacts__item">
        <svg class="contacts__icon" viewBox="0 0 24 24"><rect width="24" height="24" rx="4" fill="var(--gold)"/><rect x="5" y="7" width="14" height="10" fill="none" stroke="#fff" stroke-width="1.6"/><path d="M5 7 L12 13 L19 7" fill="none" stroke="#fff" stroke-width="1.6"/></svg>
        <span>info@harbourlinegroup.com.au</span>
      </li>
      <li class="contacts__item">
        <svg class="contacts__icon" viewBox="0 0 24 24"><rect width="24" height="24" rx="4" fill="var(--gold)"/><circle cx="12" cy="12" r="6.5" fill="none" stroke="#fff" stroke-width="1.5"/><ellipse cx="12" cy="12" rx="3" ry="6.5" fill="none" stroke="#fff" stroke-width="1.2"/><path d="M5.5 12 H18.5" stroke="#fff" stroke-width="1.2"/></svg>
        <span>www.harbourlinegroup.com.au</span>
      </li>
    </ul>
  </div>
</body>
</html>
```